New Business Card Design Project

Use the flyer uploaded and website www.brightoakbuilders.com for inspiration.
List Our Services on Backside of business cards
Marcus Delling
Harborline Builders Inc.
Licensed General Contractors
858-471-6093

Contact Information for Business Card

Use the flyer uploaded and website www.brightoakbuilders.com for inspiration. List Our Services on Backside of business cards Marcus Delling Harborline Builders Inc. Licensed General Contractors 858-471-6093

```html
<!DOCTYPE html>
<html lang="en">
<head>
<meta charset="utf-8">
<title>Harborline Builders – Business Card</title>
<link href="https://fonts.googleapis.com/css2?family=Sorts+Mill+Goudy&display=swap" rel="stylesheet">
<style>
  :root {
    --backdrop: #e7e3dc;
    --card: #0e0e0e;
    --ink: #f2f2f2;
    --rule: #cfcfcf;
  }
  * { box-sizing: border-box; margin: 0; padding: 0; }
  html, body { width: 1200px; height: 900px; overflow: hidden; }
  body {
    background: var(--backdrop);
    font-family: "Sorts Mill Goudy", Georgia, serif;
    color: var(--ink);
    display: flex;
    flex-direction: column;
    align-items: center;
    justify-content: center;
    gap: 34px;
  }
  .card {
    position: relative;
    width: 700px;
    height: 400px;
    background: var(--card);
    border-radius: 38px;
    box-shadow: 0 10px 24px rgba(0,0,0,.25);
  }
  .brand {
    display: flex;
    align-items: center;
    gap: 10px;
    font-size: 22px;
    letter-spacing: 2px;
    text-transform: uppercase;
    color: var(--ink);
  }
  .brand-dot {
    width: 10px; height: 10px;
    border: 1px solid var(--ink);
    border-radius: 50%;
  }

  /* services side */
  .card-services {
    display: flex;
    flex-direction: column;
    align-items: center;
    padding-top: 78px;
    text-align: center;
  }
  .services-title {
    margin-top: 44px;
    font-size: 22px;
    letter-spacing: 2px;
  }
  .services-list {
    list-style: none;
    margin-top: 22px;
    font-size: 17px;
    line-height: 1.62;
  }

  /* contact side */
  .card-contact .brand {
    position: absolute;
    top: 96px;
    right: 70px;
  }
  .top-rule {
    position: absolute;
    top: 150px;
    right: 58px;
    width: 430px;
    border-top: 1px solid var(--rule);
  }
  .person {
    position: absolute;
    left: 60px;
    top: 222px;
    display: flex;
    align-items: center;
    gap: 16px;
  }
  .person-name {
    font-size: 22px;
    letter-spacing: 2px;
    text-transform: uppercase;
  }
  .person-rule {
    width: 190px;
    border-top: 1px solid var(--rule);
  }
  .cta {
    position: absolute;
    left: 60px;
    top: 268px;
    font-size: 26px;
  }
  .contact-lines {
    position: absolute;
    left: 60px;
    top: 312px;
    list-style: none;
    font-size: 19px;
    line-height: 1.5;
  }
  .contact-lines li { display: flex; align-items: center; gap: 10px; }
  .contact-lines svg { width: 16px; height: 16px; }
  .company {
    position: absolute;
    right: 54px;
    top: 250px;
    text-align: right;
    font-size: 18px;
    line-height: 1.35;
  }
</style>
</head>
<body>

  <section class="card card-services">
    <div class="brand"><span class="brand-dot"></span>Harborline Builders</div>
    <h2 class="services-title">OUR&nbsp; SERVICES</h2>
    <ul class="services-list">
      <li>Remodel - Kitchen &amp; Bath / Painting - Interior &amp; Exterior</li>
      <li>Flooring - Carpet, Vinyl, Wood / Window &amp; Door Replacement</li>
      <li>Plumbing - Repairs &amp; Upgrades / Energy - Efficient Upgrades</li>
      <li>Deck &amp; Patio Construction / Water &amp; Mold Damage / Garage Renovation</li>
    </ul>
  </section>

  <section class="card card-contact">
    <div class="brand"><span class="brand-dot"></span>Harborline Builders</div>
    <div class="top-rule"></div>

    <div class="person">
      <span class="person-name">Marcus Delling</span>
      <span class="person-rule"></span>
    </div>
    <p class="cta">Call/Text Or Book Online</p>
    <ul class="contact-lines">
      <li>
        <svg viewBox="0 0 16 16" fill="none" stroke="currentColor" stroke-width="1.4">
          <path d="M3 2h3l1 3-2 1.2a8 8 0 0 0 4.8 4.8L11 9l3 1v3a1 1 0 0 1-1 1A11 11 0 0 1 2 3a1 1 0 0 1 1-1z"/>
        </svg>
        858-471-6093
      </li>
      <li>
        <svg viewBox="0 0 16 16" fill="none" stroke="currentColor" stroke-width="1.2">
          <circle cx="8" cy="8" r="6.5"/>
          <ellipse cx="8" cy="8" rx="3" ry="6.5"/>
          <path d="M1.5 8h13M2.5 4.8h11M2.5 11.2h11"/>
        </svg>
        www.brightoakbuilders.com
      </li>
    </ul>

    <div class="company">
      <p>Harborline Builders Inc.</p>
      <p>Licensed General Contractors</p>
    </div>
  </section>

</body>
</html>
```